Business Cards for a law firm

Business cards for our law firm. Use our silhoette logo and OAK PARTNERS - check our website (www.oakpartners.example)

Contact Information for Business Card

our silhouette logo, OAK PARTNERS, 800-555-0147, Dorian Pemberton, dorian@oakpartners.example

Requirements
Must have
• our silhouette logo, OAK PARTNERS, 800-555-0147, Dorian Pemberton, dorian@oakpartners.example

```html
<!DOCTYPE html>
<html lang="en">
<head>
<meta charset="utf-8">
<title>Oak Partners — Business Cards</title>
<link rel="stylesheet" href="https://fonts.googleapis.com/css2?family=Cinzel:wght@500;700&display=swap">
<style>
  :root {
    --stage: #5e5e5e;
    --navy: #263573;
    --navy-deep: #1e2b66;
    --ink: #1f2d68;
    --paper: #ffffff;
    --figure-fill: #27377a;
  }
  * { margin: 0; padding: 0; box-sizing: border-box; }
  html, body { width: 900px; height: 1200px; overflow: hidden; }
  body {
    background: var(--stage);
    position: relative;
    font-family: "Cinzel", serif;
    color: var(--ink);
  }
  .card {
    position: absolute;
    left: 133px;
    width: 633px;
    height: 364px;
  }
  .card-front { top: 210px; background: var(--navy); }
  .card-back { top: 624px; background: var(--paper); }

  .front-mark {
    position: absolute;
    left: 60px; top: 140px;
    width: 40px; height: 40px;
    background: var(--navy-deep);
  }
  .front-name {
    position: absolute;
    left: 142px; top: 150px;
    font-size: 48px; font-weight: 700;
    letter-spacing: 1px;
    color: var(--navy-deep);
    line-height: 1;
    white-space: nowrap;
  }

  .back-name {
    position: absolute;
    left: 40px; top: 44px;
    font-size: 32px; font-weight: 700;
    letter-spacing: 1px; line-height: 1;
    white-space: nowrap;
  }
  .person {
    position: absolute;
    left: 40px; top: 178px;
  }
  .person-name {
    font-size: 28px; font-weight: 700;
    letter-spacing: 0.5px; line-height: 1;
  }
  .person-role {
    margin-top: 6px;
    font-size: 16px; font-weight: 500;
    letter-spacing: 1px; line-height: 1;
  }
  .contact {
    position: absolute;
    left: 40px; top: 245px;
    list-style: none;
  }
  .contact li {
    display: flex; align-items: center;
    height: 16px; margin-bottom: 11px;
    font-weight: 500; line-height: 1;
  }
  .contact svg { width: 15px; height: 15px; margin-right: 4px; fill: var(--ink); flex: none; }
  .contact .phone { font-size: 16px; letter-spacing: 3px; }
  .contact .email, .contact .web { font-size: 13px; letter-spacing: 0.5px; }

  .figures {
    position: absolute;
    left: 416px; top: 49px;
    width: 178px; height: 269px;
    background: linear-gradient(180deg, #2e3f86, var(--figure-fill));
    border-radius: 4px;
  }
</style>
</head>
<body>
  <section class="card card-front" aria-label="Card front">
    <div class="front-mark"></div>
    <div class="front-name">OAK PARTNERS</div>
  </section>

  <section class="card card-back" aria-label="Card back">
    <div class="back-name">OAK PARTNERS</div>
    <div class="person">
      <div class="person-name">DORIAN PEMBERTON</div>
      <div class="person-role">ATTORNEY</div>
    </div>
    <ul class="contact">
      <li class="phone">
        <svg viewBox="0 0 24 24" aria-hidden="true"><path d="M6.6 10.8c1.4 2.8 3.8 5.1 6.6 6.6l2.2-2.2c.3-.3.7-.4 1-.2 1.1.4 2.3.6 3.6.6.6 0 1 .4 1 1V20c0 .6-.4 1-1 1C10.6 21 3 13.4 3 4c0-.6.4-1 1-1h3.5c.6 0 1 .4 1 1 0 1.3.2 2.5.6 3.6.1.3 0 .7-.2 1l-2.3 2.2z"/></svg>
        800-555-0147
      </li>
      <li class="email">
        <svg viewBox="0 0 24 24" aria-hidden="true"><path d="M2 5h20v14H2z" fill="none"/><path d="M2 5h20l-10 8z"/><path d="M2 7l10 8 10-8v12H2z"/></svg>
        DORIAN@OAKPARTNERS.EXAMPLE
      </li>
      <li class="web">
        <svg viewBox="0 0 24 24" aria-hidden="true"><path d="M12 2a10 10 0 100 20 10 10 0 000-20zm6.9 6h-2.9a15 15 0 00-1.4-3.6A8 8 0 0118.9 8zM12 4c.8 1.2 1.5 2.5 1.9 4h-3.8c.4-1.5 1.1-2.8 1.9-4zM4.3 14a8 8 0 010-4h3.3a16 16 0 000 4H4.3zm.8 2h2.9c.3 1.3.8 2.5 1.4 3.6A8 8 0 015.1 16zM8 8H5.1a8 8 0 014.3-3.6C8.8 5.5 8.4 6.7 8 8zm4 12c-.8-1.2-1.5-2.5-1.9-4h3.8c-.4 1.5-1.1 2.8-1.9 4zm2.3-6H9.7a14 14 0 010-4h4.6a14 14 0 010 4zm.3 5.6c.6-1.1 1.1-2.3 1.4-3.6h2.9a8 8 0 01-4.3 3.6zm1.8-5.6a16 16 0 000-4h3.3a8 8 0 010 4h-3.3z"/></svg>
        WWW.OAKPARTNERS.EXAMPLE
      </li>
    </ul>
    <div class="figures" role="img" aria-label="Silhouette illustration of two standing men in suits"></div>
  </section>
</body>
</html>
```